Veltrane Group Business Card Design

The CEO is looking for a new trendy look for his business card.
You can stay with current branding or come up with something new/creative. It can be 3D, including Medical Office buildings. You can use our logo in a variety of colors. Please include name, title, company name, company website, email address, cell number

Target Market(s)

Real Estate Development and Construction

Industry/Entity Type

Health care real estate

Contact Information for Business Card

Rohesh Kamdar, CEO M-604.781.2249 E-roheshkamdar@veltrane.com Address:4180 Lindqvist Ave, Tampa, FL 33482 www.veltrane.com

Font styles to use
Other font styles liked:
• Be creative

Requirements
Must have
• Creative, trendy look
Nice to have
• Please go to our website to get a feel- www. veltrane.com
Should not have
• small fonts

```html
<!DOCTYPE html>
<html lang="en">
<head>
<meta charset="utf-8">
<title>Veltrane Group — Business Card</title>
<link rel="stylesheet" href="https://fonts.googleapis.com/css2?family=Montserrat:wght@400;600;700;800&display=swap">
<style>
  :root {
    --brand-red: #b01f28;
    --brand-navy: #1c2f52;
    --card-black: #181818;
    --card-white: #ffffff;
    --backdrop: #dcdcda;
    --text-light: #ffffff;
  }
  * { box-sizing: border-box; margin: 0; padding: 0; }
  html, body { width: 1200px; height: 801px; overflow: hidden; }
  body {
    background: var(--backdrop);
    font-family: "Montserrat", Arial, sans-serif;
    position: relative;
  }
  .card {
    position: absolute;
    top: 246px;
    width: 540px;
    height: 309px;
    background: var(--card-white);
    overflow: hidden;
    box-shadow: 0 6px 18px rgba(0,0,0,0.18);
  }
  .card--front { left: 45px; }
  .card--back { left: 615px; border-bottom: 2px solid var(--brand-red); }
  .wave { position: absolute; inset: 0; width: 100%; height: 100%; }
  .wordmark {
    position: absolute;
    color: var(--brand-red);
    font-weight: 800;
    letter-spacing: -0.5px;
    white-space: nowrap;
    line-height: 1;
  }
  .card--front .wordmark { top: 30px; right: 26px; font-size: 40px; }
  .card--back .wordmark {
    top: 50%; left: 50%;
    transform: translate(-50%, -50%);
    font-size: 58px;
  }
  .contact {
    position: absolute;
    left: 34px;
    bottom: 24px;
    color: var(--text-light);
  }
  .contact__accent {
    position: absolute;
    left: -34px; top: 4px;
    width: 22px; height: 34px;
    background: var(--brand-red);
  }
  .contact__name {
    color: var(--brand-red);
    font-weight: 700;
    font-size: 20px;
    letter-spacing: 0.5px;
    text-transform: uppercase;
  }
  .contact__title { font-size: 14px; margin-bottom: 10px; }
  .contact__address { font-size: 13px; line-height: 1.35; margin-bottom: 10px; }
  .contact__list { list-style: none; font-size: 13px; line-height: 1.5; }
  .contact__list li { display: flex; align-items: center; gap: 8px; }
  .contact__icon { width: 12px; height: 12px; flex: none; }
</style>
</head>
<body>
  <section class="card card--front" aria-label="Business card front">
    <svg class="wave" viewBox="0 0 540 309" preserveAspectRatio="none" aria-hidden="true">
      <g>
        <path transform="translate(0,-16)" fill="var(--brand-red)" d="M0,28 C140,110 300,150 540,235 L540,330 L0,330 Z"/>
        <path transform="translate(0,-11)" fill="var(--card-white)" d="M0,28 C140,110 300,150 540,235 L540,330 L0,330 Z"/>
        <path transform="translate(0,-9)" fill="var(--brand-navy)" d="M0,28 C140,110 300,150 540,235 L540,330 L0,330 Z"/>
        <path transform="translate(0,-3)" fill="var(--card-white)" d="M0,28 C140,110 300,150 540,235 L540,330 L0,330 Z"/>
        <path fill="var(--card-black)" d="M0,28 C140,110 300,150 540,235 L540,330 L0,330 Z"/>
      </g>
    </svg>
    <div class="wordmark">Veltrane Group</div>
    <div class="contact">
      <span class="contact__accent"></span>
      <h1 class="contact__name">Rohesh Kamdar</h1>
      <p class="contact__title">CEO</p>
      <p class="contact__address">4180 Lindqvist Ave,<br>Tampa, FL 33482</p>
      <ul class="contact__list">
        <li>
          <svg class="contact__icon" viewBox="0 0 12 12" aria-hidden="true"><rect x="3" y="0.5" width="6" height="11" rx="1" fill="none" stroke="var(--brand-red)" stroke-width="1.2"/><circle cx="6" cy="9.5" r="0.7" fill="var(--brand-red)"/></svg>
          604.781.2249
        </li>
        <li>
          <svg class="contact__icon" viewBox="0 0 12 12" aria-hidden="true"><rect x="0.5" y="2" width="11" height="8" fill="var(--brand-red)"/><path d="M0.5,2 L6,6.5 L11.5,2" fill="none" stroke="var(--card-black)" stroke-width="1"/></svg>
          roheshkamdar@veltrane.com
        </li>
        <li>
          <svg class="contact__icon" viewBox="0 0 12 12" aria-hidden="true"><circle cx="6" cy="6" r="5.5" fill="var(--brand-red)"/><path d="M0.5,6 H11.5 M6,0.5 C3,3 3,9 6,11.5 M6,0.5 C9,3 9,9 6,11.5" fill="none" stroke="var(--card-black)" stroke-width="0.8"/></svg>
          www.veltrane.com
        </li>
      </ul>
    </div>
  </section>

  <section class="card card--back" aria-label="Business card back">
    <div class="wordmark">Veltrane Group</div>
  </section>
</body>
</html>
```